The quiet harbor with an elephant incorporated in the background

Target Market(s)

Real estate

Industry/Entity Type

Real Estate

Contact Information for Business Card

On back on want my name & number
In front I want the business name, "the quiet harbor", below to say staging & design

Logo Text

The quiet harbor

Font styles to use
Serif

Colors
000000

Requirements
Must have
• I want an elephant behind the writing in gold transperant

```html
<!DOCTYPE html>
<html lang="en">
<head>
<meta charset="utf-8">
<title>The Quiet Harbor – Business Cards</title>
<link rel="stylesheet" href="https://fonts.googleapis.com/css2?family=Cinzel:wght@400;700&family=Quicksand:wght@300&family=Open+Sans:wght@400&display=swap">
<style>
  :root {
    --card-black: #000000;
    --gold: #ffb400;
    --gold-text: #f5b21a;
    --silver: #8c8c8c;
    --muted: #5a5a5a;
    --white: #ffffff;
    --backdrop: #e9e7e3;
    --elephant-tone: #2a2418;
  }
  * { box-sizing: border-box; margin: 0; padding: 0; }
  html, body { width: 1200px; height: 900px; overflow: hidden; }
  body {
    background: var(--backdrop);
    position: relative;
    font-family: "Open Sans", sans-serif;
  }
  .card {
    position: absolute;
    width: 560px;
    height: 320px;
    background: var(--card-black);
    overflow: hidden;
    box-shadow: 0 10px 28px rgba(0,0,0,0.22);
  }
  .card--front { left: 320px; top: 110px; }
  .card--back  { left: 320px; top: 470px; }

  /* front */
  .brand {
    position: absolute;
    left: 0; right: 0; top: 92px;
    text-align: center;
  }
  .brand__mark {
    display: block;
    width: 40px; height: 40px;
    margin: 0 auto 22px;
    background: var(--gold);
  }
  .brand__name {
    font-family: "Cinzel", serif;
    font-weight: 400;
    font-size: 34px;
    color: var(--gold-text);
    letter-spacing: 1px;
    line-height: 1;
  }
  .brand__tagline {
    font-family: "Quicksand", sans-serif;
    font-weight: 300;
    font-size: 17px;
    color: var(--muted);
    letter-spacing: 1px;
    margin-top: 4px;
    padding-left: 170px;
  }

  /* back */
  .elephant-art {
    position: absolute;
    left: 330px; top: 24px;
    width: 200px; height: 190px;
    border-radius: 45% 45% 20% 20%;
    background: radial-gradient(ellipse at 50% 45%, var(--elephant-tone), rgba(42,36,24,0.35) 75%, transparent);
  }
  .swoosh { position: absolute; left: 0; top: 0; width: 560px; height: 320px; }
  .person {
    position: absolute;
    left: 40px; top: 38px;
    font-family: "Cinzel", serif;
    font-weight: 700;
    font-size: 22px;
    color: var(--gold-text);
    letter-spacing: 0.5px;
  }
  .contact {
    position: absolute;
    left: 40px; top: 118px;
    list-style: none;
    color: var(--white);
    font-size: 15px;
    line-height: 21px;
  }
  .contact__item { display: flex; align-items: center; gap: 8px; }
  .contact__icon { width: 12px; height: 12px; flex: none; }
  .address {
    position: absolute;
    left: 40px; top: 190px;
    color: var(--white);
    font-size: 15px;
    line-height: 21px;
  }
</style>
</head>
<body>

  <section class="card card--front">
    <div class="brand">
      <span class="brand__mark"></span>
      <h1 class="brand__name">The Quiet Harbor</h1>
      <p class="brand__tagline">staging &amp; design</p>
    </div>
  </section>

  <section class="card card--back">
    <div class="elephant-art" role="img" aria-label="Faint gold elephant silhouette with raised trunk"></div>

    <svg class="swoosh" viewBox="0 0 560 320" aria-hidden="true">
      <path d="M0,300 L0,248 C140,282 280,228 390,150 C450,110 510,92 560,92 L560,110 C510,112 450,130 395,170 C290,245 150,290 0,268 Z" fill="var(--silver)"/>
      <path d="M0,320 L0,276 C150,300 300,238 405,168 C465,128 520,110 560,108 L560,320 Z" fill="var(--gold)"/>
    </svg>

    <h2 class="person">Daniel Reyes</h2>

    <ul class="contact">
      <li class="contact__item">
        <svg class="contact__icon" viewBox="0 0 12 12" aria-hidden="true">
          <path d="M2.5,0.8 L4.4,3.2 L3.4,4.5 C4,6 5.8,7.8 7.5,8.6 L8.8,7.6 L11.2,9.5 L10,11.2 C5.5,11 1,6.5 0.8,2 Z" fill="var(--gold)"/>
        </svg>
        <span>(055)987654321</span>
      </li>
      <li class="contact__item">
        <svg class="contact__icon" viewBox="0 0 12 12" aria-hidden="true">
          <rect x="0.5" y="2.5" width="11" height="7.5" fill="var(--gold)"/>
          <path d="M0.8,2.8 L6,6.8 L11.2,2.8" fill="none" stroke="var(--card-black)" stroke-width="1"/>
        </svg>
        <span>hello@quietharbor.com</span>
      </li>
    </ul>

    <p class="address">1234, Address GoesHere,<br>Country name, 12345</p>
  </section>

</body>
</html>
```